Computer consultant business card

Bexil Software is a newly started computer consulting company. It's a small one-man company that provides mostly Vornix applications but also websites in collaboration with designers. I'm running this company on the side of full time university studies.

I want the final design to be clean and memorable. Be creative! :)

Some inspiration:
http://www.pixelmarta.com/design/48317
http://www.pixelmarta.com/design/2739164/business-card-design-by-frostlynk
http://www.pixelmarta.com/design/604281/business-card-design-by-koralind-vestrabanu

See attachment for my company logo.
Updates

I would like to thank everyone for submitting! I'll need a couple of days to review and ultimately select a design.

Target Market(s)

Non-technical entrepreneurs and small companies.

Industry/Entity Type

University

Requirements
Must have
• My company logo.
In any way, both colors from my logo.
First- and last name, e-mail and phone number.
Double-sided design.
Nice to have
• Something creative with the symbol in my logo

```html
<!DOCTYPE html>
<html lang="en">
<head>
<meta charset="utf-8">
<title>Bexil Software – Business Card</title>
<link rel="stylesheet" href="https://fonts.googleapis.com/css2?family=Arimo:wght@400;700&display=swap">
<style>
  :root {
    --ink: #333132;
    --brand-blue: #2279f0;
    --paper: #ffffff;
    --backdrop: #e9e7e4;
    --muted: #3a3a3a;
    --divider: #9a9a9a;
  }
  * { box-sizing: border-box; margin: 0; padding: 0; }
  html, body {
    width: 1200px; height: 823px; overflow: hidden;
    background: var(--backdrop);
    font-family: "Arimo", Arial, sans-serif;
  }
  .stage { position: relative; width: 1200px; height: 823px; }

  .card {
    position: absolute;
    width: 540px; height: 310px;
    background: var(--paper);
    box-shadow: 0 4px 14px rgba(0,0,0,0.18);
    overflow: hidden;
  }
  .card--front { left: 50px; top: 140px; }
  .card--back  { left: 610px; top: 373px; }

  /* Front */
  .brand {
    position: absolute; left: 70px; top: 56px;
    display: flex; align-items: center; gap: 26px;
  }
  .brand__dot {
    width: 92px; height: 92px; border-radius: 50%;
    background: var(--brand-blue);
  }
  .brand__name {
    font-size: 84px; font-weight: 700; color: var(--ink);
    letter-spacing: 1px; line-height: 1;
  }

  .contact {
    position: absolute; left: 0; right: 0; top: 196px;
    display: flex; justify-content: center; align-items: center;
    font-size: 15px; color: var(--muted); line-height: 1.3;
  }
  .contact__address { font-style: normal; text-align: right; padding-right: 14px; }
  .contact__divider { width: 1px; height: 44px; background: var(--divider); }
  .contact__lines { padding-left: 14px; }
  .contact__line { display: flex; align-items: center; gap: 7px; }
  .contact__line svg { width: 12px; height: 12px; fill: var(--brand-blue); }

  .rule {
    position: absolute; left: 0; right: 0; top: 254px;
    height: 3px; background: var(--ink);
  }
  .nameband {
    position: absolute; left: 0; right: 0; top: 261px; bottom: 0;
    background: var(--brand-blue);
    display: flex; align-items: center; justify-content: center;
    color: var(--paper); font-size: 19px;
  }
  .nameband strong { font-weight: 700; margin-right: 6px; }

  /* Back */
  .back-mark {
    position: absolute; inset: 0;
    display: flex; align-items: center; justify-content: center; gap: 22px;
  }
  .back-mark__dot {
    width: 120px; height: 120px; border-radius: 50%;
    background: var(--brand-blue);
  }
  .back-mark__name {
    font-size: 72px; font-weight: 700; color: var(--ink); line-height: 1;
  }
</style>
</head>
<body>
<main class="stage">

  <section class="card card--front" aria-label="Business card front">
    <div class="brand">
      <span class="brand__dot" aria-hidden="true"></span>
      <span class="brand__name">Bexil</span>
    </div>

    <div class="contact">
      <address class="contact__address">
        14, Alder Court<br>Lenford, KS 0318
      </address>
      <span class="contact__divider" aria-hidden="true"></span>
      <div class="contact__lines">
        <div class="contact__line">
          <svg viewBox="0 0 24 24" aria-hidden="true"><path d="M6.6 10.8a15.1 15.1 0 0 0 6.6 6.6l2.2-2.2a1 1 0 0 1 1-.25 11.4 11.4 0 0 0 3.6.57 1 1 0 0 1 1 1V20a1 1 0 0 1-1 1A17 17 0 0 1 3 4a1 1 0 0 1 1-1h3.5a1 1 0 0 1 1 1c0 1.25.2 2.45.57 3.57a1 1 0 0 1-.25 1z"/></svg>
          <span>0412 738596</span>
        </div>
        <div class="contact__line">
          <svg viewBox="0 0 24 24" aria-hidden="true"><path d="M2 5h20v14H2zm2 2v.4l8 5.1 8-5.1V7zm0 2.8V17h16V9.8l-8 5.1z"/></svg>
          <span>info@bexil.com</span>
        </div>
      </div>
    </div>

    <div class="rule" aria-hidden="true"></div>
    <div class="nameband"><strong>First Name,</strong> Last Name</div>
  </section>

  <section class="card card--back" aria-label="Business card back">
    <div class="back-mark">
      <span class="back-mark__dot" aria-hidden="true"></span>
      <span class="back-mark__name">Bexil</span>
    </div>
  </section>

</main>
</body>
</html>
```